Law Firm in Texas in need of new letterhead

Law Firm in Fort Worth, TX, USA named "Pell & Varnum, Attorneys-At-Law, LLP." This is a general practice law firm that mostly does Family Law and Criminal Defense work.

We are looking for a new letterhead that has a "classical" appeal, with modern elements.

Any color combination is fine, but please note that we do fax many documents, so the design must be clearly legible in Black and White.

We would like our letterhead to project a sense of professionalism, integrity, and ability.

Target Market(s)

Letterhead will be for correspondence generally with other attorneys and clients.

Industry/Entity Type

Law Firm

Logo Text

Pell & Varnum, Attorneys-At-Law, LLP.

Logo styles of interest
Pictorial/Combination Logo
Wordmark Logo
Lettermark Logo
Requirements
Nice to have
• Although not necessary, a "Texas Star" that is incorporated into the design would be a nice touch.
Should not have
• Colors that do not convert to B&W easily

```html
<!DOCTYPE html>
<html lang="en">
<head>
<meta charset="utf-8">
<title>Pell &amp; Varnum Letterhead</title>
<link href="https://fonts.googleapis.com/css2?family=Cinzel:wght@400&family=Montserrat:wght@400;600&display=swap" rel="stylesheet">
<style>
  :root {
    --backdrop: #efefef;
    --paper: #fbfbfb;
    --navy: #1f3a7a;
    --band: #1e336f;
    --accent: #2f86c8;
    --accent-light: #5aa6dc;
    --text-grey: #7a7a7a;
    --rule-navy: #3f5a9a;
  }
  * { margin: 0; padding: 0; box-sizing: border-box; }
  html, body { width: 1200px; height: 815px; overflow: hidden; }
  body { background: var(--backdrop); position: relative; font-family: "Montserrat", Arial, sans-serif; }

  .sheet { position: absolute; top: 70px; width: 484px; height: 685px; background: var(--paper); overflow: hidden; }
  .sheet--classic { left: 80px; }
  .sheet--band { left: 638px; }

  .firm-name {
    position: absolute; left: 0; width: 100%; text-align: center;
    font-family: "Cinzel", "Times New Roman", serif; font-weight: 400; color: var(--navy);
  }
  .firm-name__title { display: block; font-size: 25px; letter-spacing: 0.5px; line-height: 1; }
  .firm-name__sub { display: block; font-size: 12.5px; letter-spacing: 0.4px; line-height: 1; margin-top: 5px; }
  .firm-name__sub::before,
  .firm-name__sub::after {
    content: ""; display: inline-block; width: 16px; height: 1px;
    background: var(--navy); vertical-align: middle; margin: 0 5px;
  }
  .sheet--classic .firm-name { top: 46px; }
  .sheet--band .firm-name { top: 102px; }

  .brand-square { position: absolute; left: 217px; top: 34px; width: 50px; height: 50px; background: var(--accent); }

  .footer { position: absolute; font-size: 6.2px; line-height: 7.4px; color: var(--text-grey); }
  .footer__col { position: absolute; padding-left: 9px; border-left: 1px solid var(--rule-navy); white-space: nowrap; }
  .footer strong { font-weight: 600; color: var(--navy); }

  .sheet--classic .footer { left: 0; top: 645px; width: 100%; height: 40px; }
  .sheet--classic .footer__col { top: 0; height: 38px; padding-top: 2px; }
  .sheet--classic .col-address { left: 36px; }
  .sheet--classic .col-phone { left: 123px; }
  .sheet--classic .col-partner { left: 216px; }
  .sheet--classic .col-associate { left: 350px; }

  .band { position: absolute; left: 0; top: 636px; width: 100%; height: 49px; background: var(--band); }
  .band__accent { position: absolute; left: 0; top: 0; width: 14px; height: 100%; background: var(--accent); }
  .band__title { position: absolute; left: 37px; top: 10px; font-size: 6.2px; line-height: 7.4px; color: #ffffff; letter-spacing: 0.1px; }
  .band .footer { left: 0; top: 0; width: 100%; height: 49px; color: #dfe5f2; }
  .band .footer__col { border-left-color: var(--accent-light); }
  .band .footer strong { color: var(--accent-light); }
  .band .col-address { left: 37px; top: 23px; border-left: none; padding-left: 10px; }
  .band .col-phone { left: 124px; top: 22px; height: 17px; padding-top: 1px; }
  .band .col-partner { left: 217px; top: 9px; height: 31px; padding-top: 1px; }
  .band .col-associate { left: 350px; top: 9px; height: 17px; padding-top: 1px; }
</style>
</head>
<body>

<section class="sheet sheet--classic" aria-label="Letterhead, classic version">
  <h1 class="firm-name">
    <span class="firm-name__title">Pell &amp; Varnum</span>
    <span class="firm-name__sub">Attorneys At Law, LLP</span>
  </h1>
  <footer class="footer">
    <div class="footer__col col-address">4120 W. Rosedale Ave.<br>Fort Worth, TX 76107</div>
    <div class="footer__col col-phone"><strong>Phone:</strong> (817) 555-0142<br><strong>Fax:</strong> (817) 555-0187</div>
    <div class="footer__col col-partner"><strong>DANIEL PELL</strong> - Managing Partner<br>- Licensed in State of Texas<br>- United States District Court<br>- United States Supreme Court</div>
    <div class="footer__col col-associate"><strong>LAURA JANE VARNUM</strong><br>- Licensed in the State of Texas</div>
  </footer>
</section>

<section class="sheet sheet--band" aria-label="Letterhead, band version">
  <div class="brand-square"></div>
  <h1 class="firm-name">
    <span class="firm-name__title">Pell &amp; Varnum</span>
    <span class="firm-name__sub">Attorneys At Law, LLP</span>
  </h1>
  <div class="band">
    <div class="band__accent"></div>
    <p class="band__title">PELL &amp; VARNUM, ATTORNEYS-AT-LAW, LLP</p>
    <footer class="footer">
      <div class="footer__col col-address">4120 W. Rosedale Ave.<br>Fort Worth, TX 76107</div>
      <div class="footer__col col-phone"><strong>Phone:</strong> (817) 555-0142<br><strong>Fax:</strong> (817) 555-0187</div>
      <div class="footer__col col-partner"><strong>DANIEL PELL</strong> - Managing Partner<br>- Licensed in State of Texas<br>- United States District Court<br>- United States Supreme Court</div>
      <div class="footer__col col-associate"><strong>LAURA JANE VARNUM</strong><br>- Licensed in the State of Texas</div>
    </footer>
  </div>
</section>

</body>
</html>
```